business card deign

Logo needs the following on it.
1. attached logo
2. Tagline - "If it keeps a drink cold or the party going...we do it!"
3. Name- Dalton Pikes, Founder and CPO
4. Address - 412 E. Carver Avenue, Ste 2207, Tampa, FL. 33917
5. Phone - 555.318.4726

```html
<!DOCTYPE html>
<html lang="en">
<head>
<meta charset="utf-8">
<title>Brightpour Business Card</title>
<link rel="stylesheet" href="https://fonts.googleapis.com/css2?family=Montserrat:wght@400;600;700&display=swap">
<style>
  :root {
    --backdrop: #e8e8e8;
    --card: #222222;
    --ink: #ffffff;
    --ink-soft: #e6e6e6;
  }
  * { margin: 0; padding: 0; box-sizing: border-box; }
  html, body {
    width: 1200px; height: 1108px; overflow: hidden;
    background: var(--backdrop);
    font-family: "Montserrat", sans-serif;
    color: var(--ink);
  }
  .canvas { position: relative; width: 1200px; height: 1108px; }
  .card {
    position: absolute;
    width: 740px; height: 444px;
    background: var(--card);
  }
  .card--front { left: 241px; top: 68px; }
  .card--back { left: 248px; top: 589px; width: 739px; height: 442px; }

  .wordmark {
    position: absolute;
    font-family: "Montserrat", sans-serif;
    font-weight: 600;
    line-height: 1;
    letter-spacing: 0;
    color: var(--ink);
    white-space: nowrap;
    transform: translateX(-50%);
  }
  .card--front .wordmark { left: 559px; top: 190px; font-size: 38px; }
  .card--back .wordmark { left: 370px; top: 266px; font-size: 50px; }

  .holder { position: absolute; left: 36px; top: 220px; }
  .holder__name { font-size: 26px; font-weight: 700; line-height: 30px; }
  .holder__role { font-size: 16px; font-weight: 400; line-height: 20px; color: var(--ink-soft); }

  .divider {
    position: absolute; left: 36px; top: 274px;
    width: 659px; height: 2px; background: var(--ink);
  }

  .contacts { position: absolute; left: 36px; top: 328px; list-style: none; }
  .contacts li {
    display: flex; align-items: center; gap: 9px;
    font-size: 16px; height: 20px; margin-bottom: 12px; color: var(--ink-soft);
  }
  .contacts svg { width: 16px; height: 16px; flex: none; fill: var(--ink); }

  .address {
    position: absolute; left: 477px; top: 373px;
    font-size: 16px; line-height: 20px; font-style: normal; color: var(--ink-soft);
    white-space: nowrap;
  }

  .tagline {
    position: absolute; left: 0; right: 0; top: 385px;
    text-align: center; font-size: 16px; color: var(--ink-soft);
  }
</style>
</head>
<body>
<div class="canvas">
  <section class="card card--front">
    <div class="wordmark">Brightpour</div>

    <div class="holder">
      <div class="holder__name">Dalton Pikes</div>
      <div class="holder__role">Founder and CPO</div>
    </div>
    <div class="divider"></div>

    <ul class="contacts">
      <li>
        <svg viewBox="0 0 16 16" aria-hidden="true"><path d="M3.6 1.5l2.3 2.6-1.3 1.8c.9 2 2.4 3.6 4.5 4.6l1.8-1.3 2.6 2.3-1.4 2.2C7.4 13.3 2.7 8.6 1.5 3z"/></svg>
        <span>555.318.4726</span>
      </li>
      <li>
        <svg viewBox="0 0 16 16" aria-hidden="true"><path d="M1.5 3.5h13v1.2L8 9.2 1.5 4.7z"/><path d="M1.5 6.1L8 10.6l6.5-4.5v6.4h-13z"/></svg>
        <span>info@brightpour.com</span>
      </li>
      <li>
        <svg viewBox="0 0 16 16" aria-hidden="true"><circle cx="8" cy="8" r="6.5" fill="none" stroke="#fff" stroke-width="1.6"/><path d="M4.5 4.5c1.5 0 2 1.2 3.2 1.4.9.2.6 1.6-.4 1.8-1 .2-1.2 1.6-2.2 1.4-.8-.2-1.6-1.6-1.9-2.8zM9.8 9.2c1.2-.3 2.6.2 3.3 1.2-.7 1.5-2 2.6-3.6 3-.5-1.3-.8-3.8.3-4.2z"/></svg>
        <span>www.brightpour.com</span>
      </li>
    </ul>

    <address class="address">
      412 E. Carver Avenue, Ste 2207,<br>
      Tampa, FL. 33917
    </address>
  </section>

  <section class="card card--back">
    <div class="wordmark">Brightpour</div>
    <p class="tagline">If it keeps a drink cold or the party going...we do it</p>
  </section>
</div>
</body>
</html>
```